One page informative flyer for Florist

We are looking for a simple one page flyer. We are a florist who sell flowers, and commemorative t-shirts at graduation ceremonies, and need a flyer that can be given out to students so that they will know what is available on site. Further, we want the flyer to be editable (ie. a word template, or some other program), so that we can change the schools name, and change small bits of the copy easily.

What we are really looking for is a simple template, but we need 4 iterations of the flyer. With each of our two logos, I will need a flyer for t-shirts, and a flyer for flowers. Making 4 total. Please see breakdown below as explanation:

1, Tasselgate Flowers logo - flyer for flowers
2. Tasselgate Flowers logo - flyer for shirts
3. Mortarboard Bloom Co logo - flyer for flowers
4. Mortarboard Bloom Co logo - flyer for shirts

Please see logos for Tasselgate Flowers and Mortarboard Bloom Co attached, as well as a picture of flowers and of the shirts. Feel free to use those images or stock images.

Here is the copy:

Flowers - A variety floral arrangements will be available for purchase at our stand, located conveniently at the graduation ceremony. You can browse our selection & pre-order ahead of time at: www.mortarboardbloomco.example/index,php/test

T-Shirts - Commerative T-Shirts displaying all of the students names will be available for purchase at our stand, located conveniently at the graduation ceremony. You can pre-order ahead of time to guarantee your choice of size at: www.mortarboardbloomco.example/index.php/test

```html
<!DOCTYPE html>
<html lang="en">
<head>
<meta charset="utf-8">
<title>Tasselgate Flowers – Graduation Flyers</title>
<link rel="stylesheet" href="https://fonts.googleapis.com/css2?family=Montserrat:wght@600;700&display=swap">
<style>
  :root {
    --page-bg: #ffffff;
    --panel-top: #ffffff;
    --panel-bottom: #ebebeb;
    --copy-grey: #5a5a5a;
    --caption-grey: #838383;
    --brand-green: #6a9a36;
    --band-light: #a3cd58;
    --band-dark: #62952f;
    --swoosh-light: #9cc94e;
    --swoosh-dark: #5f932d;
    --url-white: #ffffff;
  }
  * { margin: 0; padding: 0; box-sizing: border-box; }
  html, body {
    width: 1200px; height: 888px; overflow: hidden;
    background: var(--page-bg);
    font-family: "Montserrat", Arial, sans-serif;
  }
  .canvas { position: relative; width: 1200px; height: 888px; }

  .flyer {
    position: absolute; top: 17px;
    width: 563px; height: 843px; overflow: hidden;
    background: linear-gradient(180deg, var(--panel-top) 45%, var(--panel-bottom) 100%);
  }
  .flyer--flowers { left: 20px; }
  .flyer--shirts { left: 622px; }

  .hero { position: absolute; left: 0; top: 0; width: 563px; height: 385px; }
  .hero--roses {
    background:
      radial-gradient(ellipse 60% 55% at 68% 38%, #d4171c 0%, #b8121a 35%, rgba(150,16,20,0) 75%),
      radial-gradient(ellipse 35% 30% at 28% 35%, rgba(200,24,28,0.95) 0%, rgba(200,24,28,0) 80%),
      radial-gradient(ellipse 40% 40% at 95% 85%, #2f4a1c 0%, rgba(47,74,28,0) 80%),
      radial-gradient(ellipse 45% 50% at 8% 15%, #f6f2c9 0%, rgba(246,242,201,0) 85%),
      linear-gradient(135deg, #e9eab0 0%, #c9303a 45%, #9c1418 70%, #3d5420 100%);
  }
  .hero--shirt {
    background:
      radial-gradient(ellipse 28% 45% at 50% 42%, #ffffff 0%, #f2f2f2 55%, rgba(230,230,230,0) 100%),
      radial-gradient(ellipse 70% 70% at 50% 45%, #d9d9d9 0%, #a9a9a9 60%, #7c7c7c 100%);
  }
  .hero-swoosh { position: absolute; left: 0; top: 300px; width: 563px; height: 100px; }

  .copy {
    position: absolute; left: 0; right: 0; top: 357px;
    text-align: center; color: var(--copy-grey);
    font-weight: 700; font-size: 17.5px; line-height: 20.5px;
  }

  .product-photo {
    position: absolute; border-radius: 12px;
    box-shadow: 0 6px 8px rgba(0,0,0,0.12);
  }
  .product-photo--red { left: 93px; top: 462px; width: 170px; height: 106px;
    background:
      radial-gradient(ellipse 60% 55% at 50% 50%, #b8141c 0%, #8e1a16 55%, rgba(142,26,22,0) 90%),
      linear-gradient(180deg, #e8dcc6 0%, #c49a6a 100%); }
  .product-photo--pink { left: 293px; top: 462px; width: 170px; height: 106px;
    background:
      radial-gradient(ellipse 60% 55% at 50% 50%, #e99aa8 0%, #d07f8c 55%, rgba(208,127,140,0) 90%),
      linear-gradient(180deg, #ece0cc 0%, #c49a6a 100%); }
  .product-photo--shirts { left: 168px; top: 465px; width: 212px; height: 130px;
    background:
      radial-gradient(ellipse 55% 50% at 45% 55%, #ffffff 0%, #f0f0f0 60%, rgba(220,220,220,0) 100%),
      linear-gradient(160deg, #e4e4e4 0%, #d2d2d2 100%); }

  .brand {
    position: absolute; left: 120px; width: 323px; top: 604px;
    color: var(--brand-green);
    font-weight: 700; font-size: 58px; line-height: 78px; letter-spacing: -1.5px;
  }
  .brand-line { display: block; white-space: nowrap; }
  .brand-line--first { text-align: center; }
  .brand-line--second { text-align: right; }
  .brand-mark {
    display: inline-block; width: 30px; height: 30px; border-radius: 50%;
    background: var(--brand-green); margin-right: 16px; vertical-align: 4px;
  }

  .order-note {
    position: absolute; left: 0; right: 0; top: 770px;
    text-align: center; color: var(--caption-grey);
    font-weight: 600; font-size: 14.5px;
  }

  .url-bar {
    position: absolute; left: 0; bottom: 0; width: 563px; height: 43px;
    background: linear-gradient(180deg, var(--band-light) 0%, var(--band-dark) 100%);
    color: var(--url-white); font-weight: 700; font-size: 15px;
    display: flex; align-items: center; justify-content: center;
  }
</style>
</head>
<body>
<main class="canvas">

  <section class="flyer flyer--flowers">
    <div class="hero hero--roses" role="img" aria-label="Close-up photograph of red roses in soft focus"></div>
    <svg class="hero-swoosh" viewBox="0 0 563 100" preserveAspectRatio="none" aria-hidden="true">
      <defs>
        <linearGradient id="swoosh-green-a" x1="0" y1="0" x2="1" y2="0">
          <stop offset="0" stop-color="#9cc94e"/><stop offset="1" stop-color="#5f932d"/>
        </linearGradient>
      </defs>
      <path d="M0 35 C220 26 430 38 563 80 L563 100 L0 100 Z" fill="#ffffff"/>
      <path d="M0 16 C200 8 420 16 563 60 L563 80 C430 38 220 26 0 35 Z" fill="url(#swoosh-green-a)"/>
    </svg>
    <p class="copy">A variety floral arrangements will be<br>available for purchase at our stand,<br>located conveniently at the<br>graduation ceremony</p>
    <div class="product-photo product-photo--red" role="img" aria-label="Photograph of a bouquet of red roses"></div>
    <div class="product-photo product-photo--pink" role="img" aria-label="Photograph of a bouquet of pink roses"></div>
    <div class="brand">
      <span class="brand-line brand-line--first">Tasselgate</span>
      <span class="brand-line brand-line--second"><span class="brand-mark"></span>Flowers</span>
    </div>
    <p class="order-note">You can browse our selection &amp; pre-order ahead of time at:</p>
    <div class="url-bar">www.mortarboardbloomco.example/index,php/test</div>
  </section>

  <section class="flyer flyer--shirts">
    <div class="hero hero--shirt" role="img" aria-label="Photograph of a person wearing a white college t-shirt"></div>
    <svg class="hero-swoosh" viewBox="0 0 563 100" preserveAspectRatio="none" aria-hidden="true">
      <defs>
        <linearGradient id="swoosh-green-b" x1="0" y1="0" x2="1" y2="0">
          <stop offset="0" stop-color="#9cc94e"/><stop offset="1" stop-color="#5f932d"/>
        </linearGradient>
      </defs>
      <path d="M0 35 C220 26 430 38 563 80 L563 100 L0 100 Z" fill="#ffffff"/>
      <path d="M0 16 C200 8 420 16 563 60 L563 80 C430 38 220 26 0 35 Z" fill="url(#swoosh-green-b)"/>
    </svg>
    <p class="copy">Commerative T-Shirts displaying all of<br>the students names will be available<br>for purchase at our stand, located<br>conveniently at the graduation<br>ceremony.</p>
    <div class="product-photo product-photo--shirts" role="img" aria-label="Photograph of commemorative graduation t-shirts, front and back"></div>
    <div class="brand">
      <span class="brand-line brand-line--first">Tasselgate</span>
      <span class="brand-line brand-line--second"><span class="brand-mark"></span>Flowers</span>
    </div>
    <p class="order-note">You can pre-order ahead of time to guarantee your choice of size at:</p>
    <div class="url-bar">www.mortarboardbloomco.example/index.php/test</div>
  </section>

</main>
</body>
</html>
```